Business Card for Vorla Parts Wholesale supplier

Hi There! I need a new business card for our company. We are specialized in selling Vorla parts, mostly we sell new LCD screens for Zelnar and Drelks. I would like to see that back in the design.

You can find the colors and logo's on our website: www.hartuvo.nl

Industry/Entity Type

Business

Contact Information for Business Card

My Details:
Tobias Lindqvist

Phone: 0031687203316
E-mail: Tobias@hartuvo.nl

Slogan: "Built For Every Repair"

Font styles to use
Sans Serif

Colors

Designer to choose colors to be used in the design.

Requirements
Must have
• A Black backside with the Hartuvo logo on it. The front side should be clean with only my contact details.
• But I'm also open for something really different or awesome!
Nice to have
• Remember that we are in the parts & repairing industry, So i'll be handing those business cards mainly to repair companies. Maybe you can do something with that thought :)

```html
<!DOCTYPE html>
<html lang="en">
<head>
<meta charset="UTF-8">
<title>Hartuvo Business Card</title>
<link href="https://fonts.googleapis.com/css2?family=Arimo:wght@400;700&display=swap" rel="stylesheet">
<style>
  :root {
    --backdrop: #2b2b2d;
    --card-white: #ffffff;
    --card-black: #0c0c0c;
    --brand-orange: #f26b21;
    --text-grey: #6f6f6f;
    --logo-dark: #161616;
    --logo-light: #ffffff;
  }
  * { margin: 0; padding: 0; box-sizing: border-box; }
  html, body {
    width: 1200px;
    height: 950px;
    overflow: hidden;
  }
  body {
    background: var(--backdrop);
    font-family: "Arimo", Arial, sans-serif;
    position: relative;
  }
  .card {
    position: absolute;
    left: 230px;
    width: 740px;
    height: 423px;
    overflow: hidden;
    box-shadow: 0 10px 30px rgba(0,0,0,0.45);
  }
  .card-front { top: 40px; background: var(--card-white); }
  .card-back {
    top: 487px;
    background: linear-gradient(135deg, #1c1c1c 0%, var(--card-black) 55%, #050505 100%);
  }

  .name-band {
    position: absolute;
    left: 0;
    top: 128px;
    width: 360px;
    height: 56px;
  }
  .holder-name {
    position: absolute;
    left: 40px;
    top: 145px;
    color: var(--brand-orange);
    font-size: 21px;
    font-weight: 400;
    white-space: nowrap;
  }

  .logo {
    position: absolute;
    display: flex;
    align-items: center;
    gap: 12px;
  }
  .logo-dot {
    width: 40px;
    height: 40px;
    border-radius: 50%;
    background: var(--brand-orange);
    flex: none;
  }
  .logo-name {
    font-size: 50px;
    font-weight: 700;
    letter-spacing: 1px;
    line-height: 1;
    white-space: nowrap;
  }
  .card-front .logo { left: 372px; top: 130px; }
  .card-front .logo-name { color: var(--logo-dark); }
  .card-back .logo { left: 50%; top: 50%; transform: translate(-50%, -50%); }
  .card-back .logo-dot { width: 58px; height: 58px; }
  .card-back .logo-name { color: var(--logo-light); font-size: 76px; }

  .contact-list {
    position: absolute;
    left: 225px;
    top: 228px;
    list-style: none;
    font-size: 17px;
    line-height: 31px;
    color: var(--text-grey);
    white-space: nowrap;
  }
  .contact-label {
    color: var(--brand-orange);
    display: inline-block;
    width: 32px;
  }
  .slogan {
    color: var(--brand-orange);
    font-weight: 700;
  }
</style>
</head>
<body>
  <section class="card card-front" aria-label="Front of business card">
    <svg class="name-band" viewBox="0 0 360 56" aria-hidden="true">
      <defs>
        <linearGradient id="bandShade" x1="0" y1="0" x2="0" y2="1">
          <stop offset="0" stop-color="#2a2a2a"/>
          <stop offset="1" stop-color="#0a0a0a"/>
        </linearGradient>
      </defs>
      <polygon points="0,0 360,0 340,56 0,56" fill="url(#bandShade)"/>
    </svg>
    <p class="holder-name">Tobias Lindqvist</p>

    <div class="logo">
      <span class="logo-dot" aria-hidden="true"></span>
      <span class="logo-name">hartuvo</span>
    </div>

    <ul class="contact-list">
      <li><span class="contact-label">P :</span>0031687203316</li>
      <li><span class="contact-label">E :</span>Tobias@hartuvo.nl</li>
      <li><span class="contact-label">W :</span>www.hartuvo.nl</li>
      <li class="slogan">Built For Every Repair</li>
    </ul>
  </section>

  <section class="card card-back" aria-label="Back of business card">
    <div class="logo">
      <span class="logo-dot" aria-hidden="true"></span>
      <span class="logo-name">hartuvo</span>
    </div>
  </section>
</body>
</html>
```